Business card for a Exhibition booth fabrication company

Hi. My company would like to change our corporate name card. We are an events and Exhibition stand builder company. We would like our corporate name card to resonate what we do. I need someone to create something unique that relates to the industry that I am in. The graphic designer should be creative to incorporate the elements of my industry and try to blend in well in the design of the card. Our aim is to ensure that we are unique and our card can look different from our competitors.
Updates

Target Market(s)

Marketing and events manager from all companies

Contact Information for Business Card

The business card should have the following details:
Name
Job Title
Email
Website

Colors

Designer to choose colors to be used in the design.

Requirements
Must have
• The card must be look something that is relevant to the service that I am providing. My website is: www.velmora-buildworks.com
• You can see my website to get more information on what service that I am doing
Nice to have
• On the back of my card, I would like to have a globe image with the incorporation of my company logo. This is to indicate that my services can be done in any part of the world.

```html
<!DOCTYPE html>
<html lang="en">
<head>
<meta charset="utf-8">
<title>Velmora Buildworks – Business Card</title>
<link rel="stylesheet" href="https://fonts.googleapis.com/css2?family=Montserrat:wght@600;700&family=Lora:wght@400;600&display=swap">
<style>
  :root {
    --red: #e3202a;
    --red-dark: #a8121a;
    --charcoal: #343434;
    --strip: #5e5a5a;
    --paper: #ffffff;
    --ink: #2b2b2b;
    --map-grey: #cfcfcf;
    --backdrop: #e6e6e6;
  }
  html, body {
    margin: 0;
    width: 1200px;
    height: 1000px;
    overflow: hidden;
    background: var(--backdrop);
  }
  .canvas {
    position: relative;
    width: 1200px;
    height: 1000px;
  }
  .card {
    position: absolute;
    width: 700px;
    height: 400px;
    background: var(--paper);
    box-shadow: 0 6px 20px rgba(0,0,0,.18);
    overflow: hidden;
  }
  .card-back { left: 440px; top: 50px; }
  .card-front { left: 60px; top: 530px; }
  .card-shapes { position: absolute; inset: 0; }

  /* back */
  .globe-area {
    position: absolute;
    left: 250px; top: 40px;
    width: 420px; height: 300px;
    border-radius: 50% / 45%;
    background: radial-gradient(ellipse at center, #dedede 0%, #ececec 55%, rgba(255,255,255,0) 75%);
  }
  .brand-back {
    position: absolute;
    left: 0; right: 0; top: 175px;
    display: flex; align-items: center; justify-content: center; gap: 14px;
    font-family: "Montserrat", sans-serif;
    font-weight: 700;
    font-size: 34px;
    letter-spacing: 4px;
    color: var(--ink);
  }
  .brand-dot {
    width: 22px; height: 22px; border-radius: 50%;
    background: var(--red);
  }

  /* front */
  .holder {
    position: absolute; left: 52px; top: 24px;
    color: var(--paper);
  }
  .holder-name {
    font-family: "Montserrat", sans-serif;
    font-weight: 700;
    font-size: 25px;
    letter-spacing: 2px;
    line-height: 1;
  }
  .holder-title {
    font-family: "Lora", serif;
    font-weight: 600;
    font-size: 13px;
    margin-top: 2px;
  }
  .brand-front {
    position: absolute; left: 40px; top: 170px;
    display: flex; align-items: center; gap: 10px;
    font-family: "Montserrat", sans-serif;
    font-weight: 700;
    font-size: 20px;
    letter-spacing: 2.5px;
    color: var(--ink);
  }
  .brand-front .brand-dot { width: 16px; height: 16px; }
  .contact-list {
    position: absolute; left: 430px; top: 125px;
    margin: 0; padding: 0; list-style: none;
    font-family: "Lora", serif;
    font-size: 16px;
    color: var(--paper);
  }
  .contact-list li {
    display: flex; align-items: center; gap: 12px;
    height: 26px;
  }
  .contact-icon { width: 16px; height: 16px; flex: none; }
  .address {
    position: absolute; left: 345px; top: 305px;
    font-family: "Lora", serif;
    font-weight: 600;
    font-size: 16px;
    line-height: 1.25;
    color: var(--paper);
  }
</style>
</head>
<body>
<main class="canvas">

  <section class="card card-back" aria-label="Card back">
    <div class="globe-area" role="img" aria-label="Faint grey world map showing the company works worldwide"></div>
    <div class="brand-back"><span class="brand-dot"></span><span>VELMORA BUILDWORKS</span></div>
  </section>

  <section class="card card-front" aria-label="Card front">
    <svg class="card-shapes" width="700" height="400" viewBox="0 0 700 400" aria-hidden="true">
      <polygon points="455,62 700,62 700,400 245,400" fill="var(--strip)"/>
      <polygon points="472,62 700,62 700,400 265,400" fill="var(--charcoal)"/>
      <polygon points="0,22 560,22 540,72 0,72" fill="var(--red)"/>
      <polygon points="500,72 540,72 515,88" fill="var(--red-dark)"/>
      <polygon points="500,72 540,72 530,62 510,62" fill="var(--red)"/>
      <polygon points="330,295 700,310 700,372 305,350" fill="var(--red)"/>
      <polygon points="305,350 330,360 338,352" fill="var(--red-dark)"/>
    </svg>

    <div class="holder">
      <div class="holder-name">DARA KELLAN</div>
      <div class="holder-title">Director</div>
    </div>

    <div class="brand-front"><span class="brand-dot"></span><span>VELMORA BUILDWORKS</span></div>

    <ul class="contact-list">
      <li>
        <svg class="contact-icon" viewBox="0 0 16 16" aria-hidden="true"><path d="M3 1l3 3-1.5 2a9 9 0 0 0 5.5 5.5L12 10l3 3-2 2C7 15 1 9 1 3z" fill="var(--red)"/></svg>
        <span>(555) 010-482</span>
      </li>
      <li>
        <svg class="contact-icon" viewBox="0 0 16 16" aria-hidden="true"><rect x="1" y="3" width="14" height="10" fill="var(--red)"/><path d="M1 3l7 6 7-6" stroke="var(--charcoal)" stroke-width="1.4" fill="none"/></svg>
        <span>username@velmora-buildworks.com</span>
      </li>
      <li>
        <svg class="contact-icon" viewBox="0 0 16 16" aria-hidden="true"><circle cx="8" cy="8" r="7" fill="var(--red)"/><g stroke="var(--charcoal)" stroke-width="1" fill="none"><ellipse cx="8" cy="8" rx="3" ry="7"/><path d="M1 8h14M2.5 4.5h11M2.5 11.5h11"/></g></svg>
        <span>www.velmora-buildworks.com</span>
      </li>
    </ul>

    <div class="address">1840 Harbor Lane 500<br>Brookfield, TX 40218</div>
  </section>

</main>
</body>
</html>
```